I want a business card design. the company is an infrastructure development company.

Target Market(s)

Government
real estate investors
real estate clients

Industry/Entity Type

Business

```html
<!DOCTYPE html>
<html lang="en">
<head>
<meta charset="utf-8">
<title>Vantor Hale – Business Card</title>
<link rel="stylesheet" href="https://fonts.googleapis.com/css2?family=Crimson+Pro:wght@400;600;700&display=swap">
<style>
  :root {
    --backdrop: #333233;
    --card: #ffffff;
    --brand-red: #ec1c24;
    --brand-blue: #00aeef;
    --ink: #1a1a1a;
    --muted: #8a8a8a;
    --soft: #a9a9a9;
    --rule: #555555;
    --band-text: #ffffff;
  }
  * { box-sizing: border-box; margin: 0; padding: 0; }
  html, body {
    width: 938px; height: 1200px; overflow: hidden;
    background: var(--backdrop);
    font-family: "Crimson Pro", Georgia, serif;
    color: var(--ink);
  }
  .card {
    position: absolute; left: 44px; width: 850px;
    background: var(--card);
  }
  .card--back { top: 56px; height: 523px; }
  .card--front { top: 631px; height: 517px; left: 48px; width: 844px; }

  .brand {
    position: absolute; left: 0; right: 0;
    display: flex; align-items: center; justify-content: center;
  }
  .brand__mark { background: var(--brand-red); flex: none; }
  .brand__name {
    font-weight: 600; color: var(--brand-blue);
    letter-spacing: 0.02em; line-height: 1; text-transform: uppercase;
  }
  .card--back .brand { top: 58px; gap: 16px; }
  .card--back .brand__mark { width: 42px; height: 42px; }
  .card--back .brand__name { font-size: 58px; }
  .card--front .brand { top: 165px; gap: 28px; }
  .card--front .brand__mark { width: 80px; height: 80px; }
  .card--front .brand__name { font-size: 112px; }

  .tagline {
    position: absolute; left: 0; right: 0; text-align: center;
    color: var(--muted); letter-spacing: 0.05em;
  }
  .card--back .tagline { top: 172px; font-size: 24px; }
  .card--front .tagline { top: 372px; font-size: 30px; }

  .person { position: absolute; left: 136px; top: 224px; }
  .person__name { font-size: 30px; font-weight: 700; line-height: 1.1; }
  .person__role { font-size: 17px; color: var(--soft); margin-top: 8px; }

  .divider {
    position: absolute; left: 442px; top: 247px;
    width: 2px; height: 218px; background: var(--rule);
  }

  .contact { position: absolute; font-size: 18.5px; line-height: 30.5px; }
  .contact--personal { left: 139px; top: 360px; }
  .company { position: absolute; left: 477px; top: 246px; font-size: 18.5px; line-height: 30.5px; }
  .company__name { font-weight: 700; }
  .company__name .first { color: var(--brand-blue); }
  .company__name .last { color: var(--brand-red); }
  .company .contact { position: static; margin-top: 10px; }

  .web-band {
    position: absolute; left: 0; right: 0; bottom: 0;
    background: var(--brand-red); color: var(--band-text);
    text-align: center; letter-spacing: 0.08em;
  }
  .card--back .web-band { height: 45px; line-height: 45px; font-size: 23px; }
  .card--front .web-band { height: 43px; line-height: 43px; font-size: 23px; }
</style>
</head>
<body>

<section class="card card--back">
  <div class="brand">
    <span class="brand__mark"></span>
    <span class="brand__name">Vantor Hale</span>
  </div>
  <p class="tagline">Infrastructure Development</p>

  <div class="person">
    <h1 class="person__name">Kayode Adeyemi</h1>
    <p class="person__role">Managing Director</p>
  </div>
  <div class="contact contact--personal">
    <p>Ph: +234 8015550142</p>
    <p>Ph: +234 7065550318</p>
    <p>Mail: kadeyemi@vantorhale.com</p>
  </div>

  <div class="divider"></div>

  <div class="company">
    <p class="company__name"><span class="first">Vantor</span> <span class="last">Hale</span></p>
    <p>12, Olumide Close, Off Allen Avenue,</p>
    <p>Ikeja Lagos, Nigeria</p>
    <div class="contact">
      <p>Ph: +234 15550276</p>
      <p>Ph: +234 7045550981</p>
      <p>Mail:&nbsp; info@vantorhale.com</p>
    </div>
  </div>

  <div class="web-band">www.vantorhale.com</div>
</section>

<section class="card card--front">
  <div class="brand">
    <span class="brand__mark"></span>
    <span class="brand__name">Vantor Hale</span>
  </div>
  <p class="tagline">Infrastructure Development</p>
  <div class="web-band">www.vantorhale.com</div>
</section>

</body>
</html>
```